Impack Proof Screen Protector Packaging Design Project

I want a sleek box design for an Impact Proof Screen Protection Shield" for mobile phones and tablet screens. Want to use this design for online website sale (eCommerce). Please use the colour combination which can effect customers physiology immediately.
Product Features:
Name: vemu Tallguard
Advanced Impact Protection Shield
Easy and Fast Application
Compatible With Stylus
Guaranteed Glue Free
Perfect Crystal Clear
Anti Fingerprint
No Air Bubble
Anti Bacterial
Anti scratch

come on guys...give me some best designs please

Project Deadline Extended
Reason: Have not received the best design yet...

Project Deadline Extended
Reason: still waiting for the best design

Project Deadline Extended

Project Deadline Extended

Project Deadline Extended

Hi,

Thanks for the design. I would like to make some changes.

I want main core colour black (HTML code of Black is 111C24)
Blue colour as aditional or second colour, (HTML code of BLUE is 0088CE)

AND another colour like Orange (HTML -> FF5800)  or Purple (HTML -> 9B1889) can be use as a ACCENT colour if needed.

Pure White, Silver and Greys like -> HTML codes -> 4D4F53 , D1D4D3 , AND C4D9E4 Can be use as support colours if needed.

please work on it and get back to me .

Thanks

Project Deadline Extended
Reason: work pending

UK & Europe is priority and then Global market

Online

• All features must write with Pictures/thumbnail on back side.
Must have a hanger hook / hole.
Must have Recycling sign/logo on the edge.
Must have our website name "vemu.co" on somewhere
its a sleek box design, size - This packing will be in 2 sizes:
a). 27cm X 11cm X 2cm
b). 25cm X 20cm X 2cm
• Impact Protection is main feature in this product, so can be highlighted with some weapon like sword or something like this...
• Please try to not use a picture of any device like lumapad etc. because this packing will be use for number of different king of mobile phone/tablet devices.

```html
<!DOCTYPE html>
<html lang="en">
<head>
<meta charset="utf-8">
<title>vemu Tallguard – Box Front</title>
<link rel="stylesheet" href="https://fonts.googleapis.com/css2?family=Roboto+Condensed:wght@400;700&family=Open+Sans:wght@300&display=swap">
<style>
  :root {
    --black: #111c24;
    --black-deep: #06090c;
    --blue: #0088ce;
    --blue-light: #4fb6e6;
    --blue-dark: #005f91;
    --grey-dark: #4d4f53;
    --silver: #d1d4d3;
    --ice: #c4d9e4;
    --white: #ffffff;
    --stage: #f2f3f4;
  }
  * { box-sizing: border-box; margin: 0; padding: 0; }
  html, body { width: 1200px; height: 1200px; overflow: hidden; }
  body { background: var(--stage); position: relative; font-family: "Roboto Condensed", Arial, sans-serif; }

  .package { position: absolute; left: 170px; top: 140px; width: 860px; height: 880px; }

  .hanger-tab {
    position: absolute; left: 0; top: 0; width: 770px; height: 200px;
    background: linear-gradient(160deg, #1a2630 0%, var(--black) 45%, var(--black-deep) 100%);
    border-radius: 10px 10px 0 0;
  }
  .hang-slot {
    position: absolute; left: 300px; top: 70px; width: 170px; height: 44px;
    background: var(--stage); border-radius: 22px;
  }

  .front-panel {
    position: absolute; left: 0; top: 200px; width: 770px; height: 680px;
    background: var(--black); overflow: hidden;
    border-top: 2px solid #2a3640;
  }
  .front-art {
    position: absolute; inset: 0;
    background:
      radial-gradient(ellipse 260px 520px at 210px 470px, rgba(0,136,206,0.85) 0%, rgba(0,136,206,0.25) 45%, transparent 70%),
      radial-gradient(ellipse 420px 260px at 120px 300px, rgba(209,212,211,0.28) 0%, transparent 70%),
      linear-gradient(150deg, #1c2833 0%, var(--black) 50%, var(--black-deep) 100%);
  }

  .brand-name {
    position: absolute; left: 150px; top: 20px; width: 590px;
    font-size: 190px; font-weight: 700; line-height: 1; letter-spacing: 2px;
    color: var(--blue); text-align: center;
  }
  .product-name {
    position: absolute; right: 40px; top: 210px;
    font-size: 70px; font-weight: 700; color: var(--white); line-height: 1;
  }
  .product-tagline {
    position: absolute; right: 40px; top: 292px;
    font-family: "Open Sans", Arial, sans-serif; font-weight: 300;
    font-size: 30px; color: var(--silver); white-space: nowrap;
  }

  .feature-grid {
    position: absolute; left: 28px; top: 395px;
    display: grid; grid-template-columns: repeat(3, 104px); gap: 22px 18px;
  }
  .feature-badge {
    width: 104px; height: 104px; border-radius: 16px;
    border: 4px solid var(--silver);
    background: linear-gradient(180deg, var(--blue-light) 0%, var(--blue) 55%, var(--blue-dark) 100%);
    display: flex; flex-direction: column; align-items: center; justify-content: flex-end;
    padding: 6px 4px 10px; text-align: center;
  }
  .feature-icon { width: 38px; height: 38px; margin-bottom: 5px; flex: none; }
  .feature-label { font-size: 12.5px; font-weight: 700; line-height: 1.1; color: var(--white); }

  .shield-area {
    position: absolute; left: 480px; top: 395px; width: 200px; height: 240px;
    border-radius: 14px;
    background: linear-gradient(120deg, var(--silver) 0%, var(--ice) 40%, var(--blue) 80%, var(--blue-dark) 100%);
    opacity: 0.9;
  }
  .recycle-area {
    position: absolute; left: 650px; top: 580px; width: 80px; height: 80px;
    border-radius: 10px;
    background: linear-gradient(135deg, var(--silver) 0%, var(--grey-dark) 100%);
    opacity: 0.75;
  }

  .side-panel {
    position: absolute; left: 770px; top: 200px; width: 90px; height: 680px;
    background: linear-gradient(90deg, #0b1218 0%, var(--black) 100%);
    border-left: 1px solid #2a3640;
  }
  .side-site {
    position: absolute; left: 50%; top: 50%;
    transform: translate(-50%, -50%) rotate(90deg);
    font-family: "Open Sans", Arial, sans-serif; font-weight: 300;
    font-size: 44px; color: var(--white); white-space: nowrap;
  }
</style>
</head>
<body>
  <div class="package">
    <div class="hanger-tab">
      <div class="hang-slot"></div>
    </div>

    <section class="front-panel">
      <div class="front-art" role="img" aria-label="Flowing black, silver and blue abstract swoosh background"></div>

      <div class="brand-name">vemu</div>
      <h1 class="product-name">Tallguard</h1>
      <p class="product-tagline">Advanced Impact Protection Shield</p>

      <div class="feature-grid">
        <div class="feature-badge">
          <svg class="feature-icon" viewBox="0 0 40 40" aria-hidden="true"><path d="M12 6 L12 30 L18 24 L22 34 L26 32 L22 22 L30 22 Z" fill="#fff"/></svg>
          <span class="feature-label">Easy and Fast Application</span>
        </div>
        <div class="feature-badge">
          <svg class="feature-icon" viewBox="0 0 40 40" aria-hidden="true"><path d="M20 5 Q31 19 31 25 A11 11 0 0 1 9 25 Q9 19 20 5 Z" fill="none" stroke="#fff" stroke-width="3"/></svg>
          <span class="feature-label">Guaranteed Glue Free</span>
        </div>
        <div class="feature-badge">
          <svg class="feature-icon" viewBox="0 0 40 40" aria-hidden="true"><path d="M20 4 L23 17 L36 20 L23 23 L20 36 L17 23 L4 20 L17 17 Z" fill="#fff"/></svg>
          <span class="feature-label">Perfect Crystal Clear</span>
        </div>
        <div class="feature-badge">
          <svg class="feature-icon" viewBox="0 0 40 40" aria-hidden="true"><g fill="none" stroke="#fff" stroke-width="2.5" stroke-linecap="round"><path d="M11 30 Q9 14 20 10 Q31 14 29 30"/><path d="M16 32 Q14 18 20 16 Q26 18 24 32"/><path d="M20 22 L20 33"/></g></svg>
          <span class="feature-label">Anti-Fingerprint</span>
        </div>
        <div class="feature-badge">
          <svg class="feature-icon" viewBox="0 0 40 40" aria-hidden="true"><circle cx="20" cy="20" r="8" fill="#fff"/><g stroke="#fff" stroke-width="3" stroke-linecap="round"><line x1="20" y1="4" x2="20" y2="9"/><line x1="20" y1="31" x2="20" y2="36"/><line x1="4" y1="20" x2="9" y2="20"/><line x1="31" y1="20" x2="36" y2="20"/></g></svg>
          <span class="feature-label">Anti-Bacterial</span>
        </div>
        <div class="feature-badge">
          <svg class="feature-icon" viewBox="0 0 40 40" aria-hidden="true"><rect x="7" y="7" width="26" height="26" rx="4" fill="none" stroke="#fff" stroke-width="3"/><path d="M13 14 L27 20 L15 27" fill="none" stroke="#fff" stroke-width="2.5" stroke-linecap="round"/></svg>
          <span class="feature-label">Anti-Scratch</span>
        </div>
      </div>

      <div class="shield-area" role="img" aria-label="Illustration of a silver and blue protective shield"></div>
      <div class="recycle-area" role="img" aria-label="Recycling sign"></div>
    </section>

    <aside class="side-panel">
      <span class="side-site">vemu.co</span>
    </aside>
  </div>
</body>
</html>
```